Im open to ideas.. I was thinking on my business cards aswell as my logo. a place for my name. email. phone number and abn..

ive attched a file with my business logo. which i dont love the colours.. i was think a dark background with charcoal letters so something along those colour schumes but im open to ideas..

BRM Constructions

```html
<!DOCTYPE html>
<html lang="en">
<head>
<meta charset="utf-8">
<title>BRM Constructions – Business Cards</title>
<link rel="stylesheet" href="https://fonts.googleapis.com/css2?family=Roboto:wght@400;700&display=swap">
<style>
  :root {
    --canvas-bg: #e9e7e3;
    --card-black: #0d0d0d;
    --card-white: #ffffff;
    --charcoal: #3a3a3a;
    --mid-grey: #6b6b6b;
    --light-grey: #b9b9b9;
    --accent-red: #e0262b;
    --edge-dark: #2a2a2a;
  }
  * { box-sizing: border-box; margin: 0; padding: 0; }
  html, body {
    width: 1200px;
    height: 950px;
    overflow: hidden;
    background: var(--canvas-bg);
    font-family: "Roboto", Arial, sans-serif;
  }
  .card-set {
    position: relative;
    width: 1200px;
    height: 950px;
    display: flex;
    flex-direction: column;
    align-items: center;
    justify-content: center;
    gap: 60px;
  }
  .card {
    position: relative;
    width: 630px;
    height: 360px;
    border-radius: 4px;
    overflow: hidden;
    box-shadow: 0 10px 24px rgba(0,0,0,0.18);
  }

  /* Back of card */
  .card--back {
    background: var(--card-black);
    display: flex;
    flex-direction: column;
    align-items: center;
    justify-content: center;
    gap: 22px;
  }
  .brand {
    display: flex;
    align-items: center;
    gap: 14px;
  }
  .brand__square {
    width: 26px;
    height: 26px;
    background: var(--accent-red);
    flex: none;
  }
  .brand__name {
    font-weight: 700;
    font-size: 40px;
    letter-spacing: 1px;
    line-height: 1;
  }
  .card--back .brand__name { color: var(--light-grey); }
  .back__web {
    color: var(--mid-grey);
    font-size: 17px;
    letter-spacing: 2px;
  }

  /* Front of card */
  .card--front {
    background: var(--card-white);
  }
  .card--front .brand {
    position: absolute;
    top: 82px;
    right: 48px;
  }
  .card--front .brand__name {
    color: var(--charcoal);
    font-size: 36px;
  }
  .contact {
    position: absolute;
    left: 44px;
    bottom: 66px;
  }
  .contact__name {
    font-size: 21px;
    color: var(--accent-red);
    margin-bottom: 10px;
  }
  .contact__role {
    color: var(--charcoal);
    font-size: 17px;
  }
  .contact__line {
    font-size: 15px;
    color: var(--mid-grey);
    letter-spacing: 0.3px;
  }
  .contact__label { color: var(--accent-red); }
  .contact__sep { color: var(--mid-grey); margin: 0 6px; }
  .card__edge {
    position: absolute;
    left: 0; right: 0; bottom: 0;
    height: 24px;
    background: var(--edge-dark);
  }
</style>
</head>
<body>
  <main class="card-set">
    <section class="card card--back" aria-label="Card back">
      <div class="brand">
        <span class="brand__square"></span>
        <span class="brand__name">BRM Constructions</span>
      </div>
      <p class="back__web">www.brmbuild.com</p>
    </section>

    <section class="card card--front" aria-label="Card front">
      <div class="brand">
        <span class="brand__square"></span>
        <span class="brand__name">BRM Constructions</span>
      </div>
      <div class="contact">
        <p class="contact__name">Sam Rowe <span class="contact__role">- President</span></p>
        <p class="contact__line">
          ABN: 987654321<span class="contact__sep">|</span><span class="contact__label">P :</span> 555 0142 7781
          &nbsp;&nbsp;<span class="contact__label">E :</span> sam@brmbuild.com
        </p>
      </div>
      <div class="card__edge"></div>
    </section>
  </main>
</body>
</html>
```